Business Card Design Project

I need a business card designed from scratch. I have an existing logo that I can upload in Illustrator for modification or redesign.

The Company is called Query Lanterns http://querylanterns.com.au and we provide Search Engine Optimization services to Australian businesses. The current logo signifies an increase in visitors, profits etc...

There are no restrictions as to the redesign - colours, style etc are all open to change.

Cards will be full colour and one sided printed at http://www.cardmoxel.com.au so check their requirements for file format and sizes etc.

I will expect all original files upon completion of project.

Target Market(s)

Any business with a web site looking to improve their search engine rankings

Industry/Entity Type

Business

Requirements
Must have
• I like modern, sleek designs. Clean, not fussy, uncluttered.

```html
<!DOCTYPE html>
<html lang="en">
<head>
<meta charset="utf-8">
<title>Query Lanterns – Business Card</title>
<link href="https://fonts.googleapis.com/css2?family=Open+Sans:wght@400;600;700;800&display=swap" rel="stylesheet">
<style>
  :root {
    --page-bg: #ececec;
    --card-bg: #ffffff;
    --brand-blue: #1f6fb8;
    --band-dark: #1d3f78;
    --band-light: #2f7fc8;
    --accent-yellow: #f5c21b;
    --text-dark: #3a3a3a;
    --divider: #c9c9c9;
  }
  * { margin: 0; padding: 0; box-sizing: border-box; }
  html, body {
    width: 1200px; height: 412px; overflow: hidden;
    background: var(--page-bg);
    font-family: "Open Sans", Arial, sans-serif;
  }
  .canvas { position: relative; width: 1200px; height: 412px; }
  .card {
    position: absolute; top: 64px;
    width: 497px; height: 284px;
    background: var(--card-bg);
    box-shadow: 0 3px 10px rgba(0,0,0,0.25);
    overflow: hidden;
  }
  .card--front { left: 73px; }
  .card--back { left: 631px; }

  .accent-line {
    position: absolute; left: 0; right: 0; top: 237px; height: 3px;
    background: var(--accent-yellow);
  }
  .web-band {
    position: absolute; left: 0; right: 0; top: 241px; bottom: 0;
    background: radial-gradient(ellipse at 30% 50%, var(--band-light) 0%, var(--band-dark) 65%);
    color: #fff; font-weight: 700; font-size: 12.5px; letter-spacing: 2px;
    display: flex; align-items: center; justify-content: center;
  }

  .brand {
    position: absolute; display: flex; align-items: center; gap: 12px;
    color: var(--brand-blue); font-weight: 800; line-height: 0.95;
  }
  .brand__dot { border-radius: 50%; background: var(--accent-yellow); flex: none; }
  .brand--front { left: 120px; top: 30px; font-size: 30px; }
  .brand--front .brand__dot { width: 40px; height: 40px; }
  .brand--back { left: 120px; top: 78px; font-size: 40px; gap: 16px; }
  .brand--back .brand__dot { width: 56px; height: 56px; }

  .identity {
    position: absolute; right: 271px; top: 170px; text-align: right;
    color: var(--text-dark); font-size: 12px; line-height: 17px;
  }
  .identity__name { font-size: 17px; font-weight: 700; line-height: 22px; }
  .identity__title { font-weight: 400; font-size: 14px; }

  .divider {
    position: absolute; left: 231px; top: 168px; width: 1px; height: 52px;
    background: var(--divider);
  }
  .contact {
    position: absolute; left: 251px; top: 173px; list-style: none;
    color: var(--text-dark); font-size: 12px; line-height: 17px;
  }
  .contact li { display: flex; align-items: center; gap: 6px; }
  .contact svg { width: 10px; height: 10px; fill: var(--text-dark); flex: none; }
</style>
</head>
<body>
<main class="canvas">

  <section class="card card--front" aria-label="Card front">
    <div class="brand brand--front">
      <span class="brand__dot"></span>
      <span class="brand__name">Query<br>Lanterns</span>
    </div>

    <div class="identity">
      <div class="identity__name">Your Name / <span class="identity__title">Title</span></div>
      <div>Complex name,Street name</div>
      <div>City, State, zip code</div>
    </div>

    <div class="divider"></div>

    <ul class="contact">
      <li>
        <svg viewBox="0 0 10 10"><path d="M2 0.5 L3.6 2.6 L2.7 3.6 Q3.6 5.6 6.4 7.3 L7.4 6.4 L9.5 8 L8.3 9.5 Q2.5 8.5 0.5 1.7 Z"/></svg>
        098 765 4321
      </li>
      <li>
        <svg viewBox="0 0 10 10"><rect x="2.5" y="0.5" width="5" height="9" rx="1"/><rect x="3.5" y="1.8" width="3" height="4" fill="#fff"/></svg>
        098 765 4321
      </li>
      <li>
        <svg viewBox="0 0 10 10"><path d="M0.5 3.5 L5 0.8 L9.5 3.5 V9 H0.5 Z"/><path d="M1.2 3.8 L5 6.3 L8.8 3.8" stroke="#fff" stroke-width="0.9" fill="none"/></svg>
        enquiry@querylanterns.com.au
      </li>
    </ul>

    <div class="accent-line"></div>
    <div class="web-band">www.querylanterns.com.au</div>
  </section>

  <section class="card card--back" aria-label="Card back">
    <div class="brand brand--back">
      <span class="brand__dot"></span>
      <span class="brand__name">Query<br>Lanterns</span>
    </div>
    <div class="accent-line"></div>
    <div class="web-band">www.querylanterns.com.au</div>
  </section>

</main>
</body>
</html>
```